Plum Lantern Cannabis Cartridge box

Box with both inside and outside box. A disposable cannabis vape cart is the contents of the package. initial thoughts were black exterior box with color highlight. (example of Jiva gum attached). There are four colors currently being used for the actual product. Black, White, Green and Blue. product will sit in retail display box. It should both "pop" and still emote quality and class.

Target Market(s)

Professional, discreet cannabis consumer. Experienced and knowledgeable

Industry/Entity Type

Cannabis

Font styles to use
Serif

Colors

Designer to choose colors to be used in the design.

Requirements
Must have
• use logo and logo colors
Nice to have
• elegant look. metalic foil printing, embossing available

```html
<!DOCTYPE html>
<html lang="en">
<head>
<meta charset="utf-8">
<title>Plum Lantern – Cartridge Box Dieline</title>
<link rel="stylesheet" href="https://fonts.googleapis.com/css2?family=Cinzel:wght@700&display=swap">
<style>
  :root {
    --paper: #ffffff;
    --ink-black: #000000;
    --brand-green: #00a886;
    --brand-blue: #0a86c8;
    --deep-blue: #0a5a8c;
    --highlight-white: #ffffff;
    --die-red: #e2463c;
  }
  html, body {
    margin: 0;
    padding: 0;
    width: 840px;
    height: 1200px;
    overflow: hidden;
    background: var(--paper);
  }
  .dieline-sheet {
    display: block;
    width: 840px;
    height: 1200px;
  }
  .bleed-shape { fill: var(--ink-black); stroke: var(--ink-black); stroke-width: 28; stroke-linejoin: round; }
  .cut-line { fill: none; stroke: var(--die-red); stroke-width: 0.8; }
  .crease-line { stroke: var(--die-red); stroke-width: 0.6; fill: none; }
  .window-cutout { fill: var(--highlight-white); stroke: var(--die-red); stroke-width: 0.8; }
  .brand-name {
    font-family: "Cinzel", Georgia, serif;
    font-weight: 700;
    fill: var(--brand-green);
    text-anchor: middle;
    letter-spacing: 1px;
  }
  .brand-mark { fill: none; stroke: var(--brand-green); stroke-width: 3; }
</style>
</head>
<body>
<svg class="dieline-sheet" viewBox="0 0 840 1200" xmlns="http://www.w3.org/2000/svg">
  <defs>
    <linearGradient id="colour-field-gradient" x1="0" y1="0" x2="0" y2="1">
      <stop offset="0" stop-color="var(--ink-black)"/>
      <stop offset="0.35" stop-color="var(--deep-blue)"/>
      <stop offset="0.6" stop-color="var(--brand-blue)"/>
      <stop offset="1" stop-color="var(--brand-green)"/>
    </linearGradient>
  </defs>

  <!-- Black printed carton with bleed -->
  <path class="bleed-shape" d="M331.5,141.7 L508.5,141.7 L508.5,296 L513.5,304 L535.5,252 L600,252 L615,295 L630,314 L681,314 L681,886 L630,886 L615,902 L600,947 L535.5,947 L513.5,896 L508.5,904 L508.5,1058.4 L331.5,1058.4 L331.5,904 L326.5,896 L304.5,947 L240.8,947 L225.7,902 L210,886 L158.5,886 L158.5,314 L210,314 L225.7,295 L240.8,252 L304.5,252 L326.5,304 L331.5,296 Z"/>

  <!-- Lower colour field of the body panels -->
  <rect class="colour-field" x="144.5" y="530" width="551" height="360.4" fill="url(#colour-field-gradient)" role="img" aria-label="Decorative band of green swooshes and a blue water wave with bubbles over a green base"/>

  <!-- Brand name on front and side panels -->
  <g class="front-panel-brand">
    <circle class="brand-mark" cx="420" cy="405" r="34"/>
    <text class="brand-name" x="420" y="478" font-size="30">PLUM</text>
    <text class="brand-name" x="420" y="512" font-size="30">LANTERN</text>
  </g>
  <g class="side-panel-brand">
    <text class="brand-name" x="279.7" y="468" font-size="13">PLUM</text>
    <text class="brand-name" x="279.7" y="484" font-size="13">LANTERN</text>
    <text class="brand-name" x="560.2" y="468" font-size="13">PLUM</text>
    <text class="brand-name" x="560.2" y="484" font-size="13">LANTERN</text>
  </g>

  <!-- Display window -->
  <circle class="window-cutout" cx="560" cy="776" r="27"/>

  <!-- Die cut and crease lines -->
  <g class="die-lines">
    <path class="cut-line" d="M331.5,141.7 L508.5,141.7 L508.5,296 L513.5,304 L535.5,252 L600,252 L615,295 L630,314 L681,314 L681,886 L630,886 L615,902 L600,947 L535.5,947 L513.5,896 L508.5,904 L508.5,1058.4 L331.5,1058.4 L331.5,904 L326.5,896 L304.5,947 L240.8,947 L225.7,902 L210,886 L158.5,886 L158.5,314 L210,314 L225.7,295 L240.8,252 L304.5,252 L326.5,304 L331.5,296 Z"/>
    <line class="crease-line" x1="225.7" y1="308.6" x2="225.7" y2="890.4"/>
    <line class="crease-line" x1="233" y1="308.6" x2="233" y2="890.4"/>
    <line class="crease-line" x1="326.5" y1="308.6" x2="326.5" y2="890.4"/>
    <line class="crease-line" x1="513.5" y1="308.6" x2="513.5" y2="890.4"/>
    <line class="crease-line" x1="607" y1="308.6" x2="607" y2="890.4"/>
    <line class="crease-line" x1="615" y1="308.6" x2="615" y2="890.4"/>
    <line class="crease-line" x1="233" y1="308.6" x2="607" y2="308.6"/>
    <line class="crease-line" x1="233" y1="890.4" x2="607" y2="890.4"/>
    <line class="crease-line" x1="331.5" y1="207.8" x2="508.5" y2="207.8"/>
    <line class="crease-line" x1="331.5" y1="215.6" x2="508.5" y2="215.6"/>
    <line class="crease-line" x1="331.5" y1="980" x2="508.5" y2="980"/>
    <line class="crease-line" x1="331.5" y1="991" x2="508.5" y2="991"/>
  </g>
</svg>
</body>
</html>
```